We are looking for Facebook and Instagram templates. To use both platforms we will use square images. We need a template for our posts, not the header image.
Most posts contain multiple images and we need a designoverlay in which we can embed our images.
Attached a screenshot of our website www.talurepo.be, our logo in svg and ai. The monkey is our mascotte (excact this monkey, not another).
We offer teambuildings, the style should be fun. Colors are antracite, limegreen and white. I did attache the current layout for posts but we are not happy with this.
If we could have some small design elements (like stickers) we can always create a new layout but is feels the same.
Our website is quite simple, this should also be in these post designs. Simple forms, rounded corners.
Updates

Allow more time for the designers, good work requires more time

Target Market(s)

Teambuilding

Industry/Entity Type

Teambuilding

Font styles to use
Other font styles liked:
• RobotoSlab

Requirements
Must have
• If we could have some small design elements (like stickers) we can always create a new layout but is feels the same.
Should not have
• Complex design, simple images works best for us

```html
<!DOCTYPE html>
<html lang="en">
<head>
<meta charset="utf-8">
<title>Talurepo – Teambuilding Memories Post</title>
<link href="https://fonts.googleapis.com/css2?family=Barlow+Condensed:wght@500;600;700;800;900&display=swap" rel="stylesheet">
<style>
  :root {
    --anthracite: #1e1f1f;
    --anthracite-soft: #2a2b2a;
    --lime: #9cc41c;
    --lime-bright: #a8cf22;
    --white: #ffffff;
    --paper: #f1f1ee;
    --tape: #e3d3a8;
    --ink: #1b1c1b;
  }
  * { margin: 0; padding: 0; box-sizing: border-box; }
  html, body { width: 1200px; height: 1200px; overflow: hidden; background: var(--anthracite); }
  .post {
    position: relative; width: 1200px; height: 1200px; overflow: hidden;
    background: radial-gradient(circle at 40% 45%, var(--anthracite-soft) 0%, var(--anthracite) 70%);
    font-family: "Barlow Condensed", sans-serif; color: var(--white);
  }
  .abs { position: absolute; }

  /* Logo */
  .brand {
    left: 71px; top: 53px; width: 276px; height: 94px;
    border: 2px solid rgba(255,255,255,.75);
    display: flex; align-items: center; justify-content: center; flex-direction: column;
    font-weight: 700; color: var(--white); line-height: 1; text-align: center;
  }
  .brand-name { font-size: 44px; letter-spacing: 2px; }
  .brand-sub { font-size: 26px; letter-spacing: 3px; margin-top: 2px; }

  /* Tagline sticker */
  .tag {
    left: 55px; top: 212px; width: 290px; height: 160px;
    background: var(--lime); transform: rotate(-3deg); border-radius: 14px;
    color: var(--ink); text-align: center; font-weight: 800;
    display: flex; flex-direction: column; justify-content: center; line-height: 1.05;
  }
  .tag-big { font-size: 52px; letter-spacing: .5px; }
  .tag-small { font-size: 31px; }

  /* Headline */
  .headline { left: 36px; top: 418px; width: 400px; font-weight: 800; line-height: 1; white-space: nowrap; transform: rotate(-2deg); }
  .headline span { display: block; }
  .hl-1 { font-size: 76px; color: var(--white); letter-spacing: .5px; }
  .hl-2 { font-size: 96px; color: var(--lime); margin-top: 4px; margin-left: 6px; }
  .hl-3 { font-size: 76px; color: var(--white); margin-left: 60px; margin-top: 4px; }
  .hl-underline { left: 130px; top: 684px; }

  /* Photo frames */
  .photo { background: var(--white); padding: 9px; box-shadow: 0 8px 18px rgba(0,0,0,.45); }
  .photo .fill { width: 100%; height: 100%; }
  .photo-1 { left: 409px; top: 38px; width: 428px; height: 340px; transform: rotate(-2deg); }
  .photo-1 .fill { background: linear-gradient(135deg, #3a3029, #8a6a52 55%, #2c2624); }
  .photo-2 { left: 822px; top: 44px; width: 366px; height: 400px; transform: rotate(2deg); }
  .photo-2 .fill { background: linear-gradient(160deg, #6f8a4a, #3d4f2c 60%, #8a7a5a); }
  .photo-3 { left: 448px; top: 388px; width: 404px; height: 382px; transform: rotate(-1deg); }
  .photo-3 .fill { background: linear-gradient(170deg, #5d7a3e, #2f2b2a 55%, #6a5a50); }
  .photo-4 { left: 822px; top: 402px; width: 366px; height: 404px; transform: rotate(2deg); }
  .photo-4 .fill { background: linear-gradient(165deg, #4f7236, #7a2e2a 55%, #b89a74); }
  .tape { background: var(--tape); opacity: .9; height: 36px; }

  /* Mascot placeholders */
  .mascot { background: radial-gradient(circle, var(--lime-bright) 0%, var(--lime) 55%, rgba(156,196,28,0) 70%); }
  .mascot-left { left: 14px; top: 704px; width: 170px; height: 180px; }
  .mascot-bottom { left: 688px; top: 990px; width: 176px; height: 156px; }

  /* Features strip */
  .features {
    left: 122px; top: 778px; width: 920px; height: 210px;
    background: var(--paper); border-radius: 12px;
    display: flex; align-items: center; color: var(--ink);
  }
  .feature {
    flex: 1; display: flex; flex-direction: column; align-items: center; gap: 14px;
    border-right: 2px dashed #9a9a96; height: 150px; justify-content: center;
  }
  .feature:last-child { border-right: none; }
  .feature-icon {
    width: 92px; height: 92px; border-radius: 50%; background: var(--lime);
    display: flex; align-items: center; justify-content: center;
  }
  .feature-label { font-weight: 700; font-size: 25px; line-height: 1.05; text-align: center; letter-spacing: .5px; }

  /* Call to action */
  .cta {
    left: 52px; top: 1030px; width: 500px; height: 72px;
    background: var(--lime); border-radius: 10px; transform: rotate(-1deg);
    display: flex; align-items: center; justify-content: center; gap: 18px;
    color: var(--ink); font-weight: 800; font-size: 34px; letter-spacing: .5px;
  }
  .cta-arrow { width: 40px; height: 40px; }

  /* Footer */
  .contact { left: 71px; top: 1124px; display: flex; align-items: center; gap: 12px; font-weight: 700; font-size: 30px; letter-spacing: .5px; }
  .socials { left: 330px; top: 1124px; display: flex; gap: 22px; }
  .social-dot { width: 38px; height: 38px; border-radius: 50%; background: var(--lime); }

  .corner-band { left: 0; top: 0; }
  .slogan {
    left: 896px; top: 1072px; width: 290px; transform: rotate(-6deg);
    color: var(--ink); font-weight: 800; font-size: 34px; line-height: 1.1; text-align: center; letter-spacing: .5px;
  }
</style>
</head>
<body>
<main class="post">

  <svg class="abs corner-band" width="1200" height="1200" viewBox="0 0 1200 1200" aria-hidden="true">
    <path d="M485 1200 L500 1175 L560 1160 L640 1140 L700 1130 L760 1110 L840 1090 L920 1070 L1010 1050 L1100 1030 L1200 1010 L1200 1200 Z" fill="var(--lime)"/>
    <path d="M1080 950 C1130 960 1160 990 1160 1030" stroke="#fff" stroke-width="3" stroke-dasharray="10 8" fill="none"/>
    <path d="M1150 1020 L1162 1040 L1172 1018" stroke="#fff" stroke-width="3" fill="none"/>
  </svg>

  <div class="abs brand">
    <span class="brand-name">TALUREPO</span>
    <span class="brand-sub">HET ANKER</span>
  </div>

  <div class="abs tag">
    <span class="tag-big">TEAMWORK</span>
    <span class="tag-small">MAKES THE<br>DREAM WORK</span>
  </div>

  <h1 class="abs headline">
    <span class="hl-1">TEAMBUILDING</span>
    <span class="hl-2">MEMORIES</span>
    <span class="hl-3">THAT LAST!</span>
  </h1>
  <svg class="abs hl-underline" width="280" height="20" viewBox="0 0 280 20" aria-hidden="true">
    <path d="M4 14 Q140 2 276 8" stroke="var(--lime)" stroke-width="7" stroke-linecap="round" fill="none"/>
  </svg>

  <div class="abs photo photo-1"><div class="fill" role="img" aria-label="Team photo: colleagues gathered around a table solving an escape-room puzzle"></div></div>
  <div class="abs photo photo-2"><div class="fill" role="img" aria-label="Team photo: group balancing together on a wooden platform in a forest"></div></div>
  <div class="abs photo photo-3"><div class="fill" role="img" aria-label="Team photo: large cheering group posing together in the woods"></div></div>
  <div class="abs photo photo-4"><div class="fill" role="img" aria-label="Team photo: tug-of-war in kilts on a sandy field"></div></div>
  <div class="abs tape" style="left:560px;top:20px;width:110px;transform:rotate(-4deg)"></div>
  <div class="abs tape" style="left:955px;top:28px;width:110px;transform:rotate(3deg)"></div>
  <div class="abs tape" style="left:825px;top:380px;width:90px;transform:rotate(-6deg)"></div>

  <div class="abs mascot mascot-left" role="img" aria-label="Lime green monkey mascot giving a thumbs up"></div>

  <section class="abs features">
    <div class="feature">
      <div class="feature-icon">
        <svg width="54" height="54" viewBox="0 0 54 54" fill="none" stroke="var(--ink)" stroke-width="3"><circle cx="27" cy="18" r="7"/><circle cx="13" cy="22" r="5"/><circle cx="41" cy="22" r="5"/><path d="M15 42c0-8 5-13 12-13s12 5 12 13"/><path d="M4 40c0-6 4-10 9-10M50 40c0-6-4-10-9-10"/></svg>
      </div>
      <span class="feature-label">STRONGER<br>TOGETHER</span>
    </div>
    <div class="feature">
      <div class="feature-icon">
        <svg width="54" height="54" viewBox="0 0 54 54" fill="none" stroke="var(--ink)" stroke-width="3"><circle cx="25" cy="29" r="18"/><circle cx="25" cy="29" r="10"/><circle cx="25" cy="29" r="3" fill="var(--ink)"/><path d="M25 29 L44 10 M38 10h6v6"/></svg>
      </div>
      <span class="feature-label">CHALLENGES<br>THAT CONNECT</span>
    </div>
    <div class="feature">
      <div class="feature-icon">
        <svg width="58" height="54" viewBox="0 0 58 54" fill="none" stroke="var(--ink)" stroke-width="3" stroke-linejoin="round"><path d="M4 44 L22 14 L34 34 L41 24 L54 44 Z"/><path d="M16 24 L22 28 L27 22"/></svg>
      </div>
      <span class="feature-label">OUTDOOR<br>ADVENTURES</span>
    </div>
    <div class="feature">
      <div class="feature-icon">
        <svg width="54" height="54" viewBox="0 0 54 54" fill="none" stroke="var(--ink)" stroke-width="3"><circle cx="27" cy="27" r="20"/><circle cx="20" cy="22" r="2" fill="var(--ink)"/><circle cx="34" cy="22" r="2" fill="var(--ink)"/><path d="M18 31c3 6 15 6 18 0" stroke-linecap="round"/></svg>
      </div>
      <span class="feature-label">FUN &amp; ENERGY<br>GUARANTEED</span>
    </div>
  </section>

  <div class="abs cta">
    <span>LET'S BUILD YOUR TEAM!</span>
    <svg class="cta-arrow" viewBox="0 0 40 40" fill="none" stroke="var(--ink)" stroke-width="3.5" stroke-linecap="round" stroke-linejoin="round"><path d="M8 20h24M22 10l10 10-10 10"/></svg>
  </div>

  <div class="abs contact">
    <svg width="32" height="32" viewBox="0 0 32 32" fill="none" stroke="var(--lime)" stroke-width="2.5"><circle cx="16" cy="16" r="13"/><ellipse cx="16" cy="16" rx="6" ry="13"/><path d="M3 16h26M5 9h22M5 23h22"/></svg>
    <span>TALUREPO.BE</span>
  </div>
  <div class="abs socials" aria-label="Social channels">
    <span class="social-dot"></span><span class="social-dot"></span><span class="social-dot"></span>
  </div>

  <div class="abs mascot mascot-bottom" role="img" aria-label="Winking lime green monkey mascot peeking over the edge"></div>

  <p class="abs slogan">FUN • ADVENTUROUS<br>TEAMBUILDING</p>
</main>
</body>
</html>
```